Copperleaf Roofing Business Card

This is my current business card. But I’d like to make some changes. Somewhere on the card I’d like to list some of the services we offer. Maybe on the back? But I’d still like to keep the red. White and black modern look.

-residential & commercial roofing
-Roof Repairs & Maintenance
-Storm Damage & Insurance Claims specialist
-Christmas Lights and permanent Christmas lights
Fencing. Windows. Gutters. Siding. Sheetrock, painting.

```html
<!DOCTYPE html>
<html lang="en">
<head>
<meta charset="utf-8">
<title>Copperleaf Roofing Business Card</title>
<link rel="stylesheet" href="https://fonts.googleapis.com/css2?family=Poppins:wght@400;600;700&family=Audiowide&display=swap">
<style>
  :root {
    --page: #e3e7e8;
    --card: #1a1a1b;
    --red: #e3222b;
    --white: #ffffff;
    --text: #f2f2f2;
    --faint: #262627;
  }
  * { box-sizing: border-box; margin: 0; padding: 0; }
  html, body { width: 1200px; height: 960px; overflow: hidden; background: var(--page); }
  body { position: relative; font-family: "Poppins", sans-serif; }

  .card {
    position: absolute;
    left: 250px;
    width: 702px;
    height: 400px;
    background: var(--card);
    border-left: 4px solid var(--red);
    border-bottom: 3px solid var(--red);
    overflow: hidden;
  }
  .card--front { top: 60px; }
  .card--back { top: 500px; }

  .brand { position: absolute; text-align: center; }
  .brand__mark {
    display: block;
    width: 108px; height: 108px;
    margin: 0 auto;
    border-radius: 50%;
    background: var(--red);
    border: 3px solid var(--white);
  }
  .brand__name {
    margin-top: 14px;
    font-family: "Poppins", sans-serif;
    font-weight: 700;
    font-size: 24px;
    line-height: 26px;
    letter-spacing: 1px;
    color: var(--red);
    text-transform: uppercase;
  }
  .card--front .brand { left: 0; right: 0; top: 28px; }
  .card--back .brand { left: 2px; width: 256px; top: 28px; }

  .services { position: absolute; left: 0; right: 0; top: 240px; text-align: center; }
  .services__title {
    font-weight: 600; font-size: 18px; letter-spacing: 0.5px;
    color: var(--red); line-height: 24px;
  }
  .services__list { list-style: none; }
  .services__list li { font-size: 15.5px; line-height: 23px; color: var(--text); letter-spacing: 0.4px; }

  .watermark {
    position: absolute;
    left: 406px; top: 110px;
    width: 292px; height: 292px;
    border-radius: 50%;
    border: 6px solid var(--faint);
    background: #1f1f20;
  }

  .person { position: absolute; right: 27px; top: 168px; text-align: right; }
  .person__name { font-family: "Audiowide", sans-serif; font-size: 29px; line-height: 34px; color: var(--white); letter-spacing: 0.5px; }
  .person__first { color: var(--red); margin-right: 8px; }
  .person__role { font-weight: 600; font-size: 16px; color: var(--white); margin-top: 4px; letter-spacing: 0.5px; }
  .accent-bar { position: absolute; right: 0; top: 169px; width: 20px; height: 61px; background: var(--red); }

  .contact { position: absolute; left: 20px; top: 303px; list-style: none; }
  .contact li { display: flex; align-items: center; height: 23px; font-size: 17.5px; color: var(--white); letter-spacing: 0.5px; }
  .contact svg { width: 16px; height: 16px; margin-right: 10px; flex: none; }
</style>
</head>
<body>

<section class="card card--front">
  <div class="brand">
    <span class="brand__mark"></span>
    <p class="brand__name">Copperleaf<br>Roofing Co.</p>
  </div>
  <div class="services">
    <h2 class="services__title">SERVICES WE OFFER</h2>
    <ul class="services__list">
      <li>Roof Repairs &amp; Maintenance</li>
      <li>Residential &amp; Commercial Roofing</li>
      <li>Storm Damage &amp; Insurance Claims Specialist</li>
      <li>Christmas Lights and Permanent Christmas lights</li>
      <li>Fencing. Windows. Gutters. Siding. Sheetrock, Painting</li>
    </ul>
  </div>
</section>

<section class="card card--back">
  <div class="watermark"></div>
  <div class="brand">
    <span class="brand__mark"></span>
    <p class="brand__name">Copperleaf<br>Roofing Co.</p>
  </div>
  <div class="person">
    <p class="person__name"><span class="person__first">DEAN</span>MARSH</p>
    <p class="person__role">OWNER</p>
  </div>
  <div class="accent-bar"></div>
  <ul class="contact">
    <li>
      <svg viewBox="0 0 24 24" fill="#e3222b"><path d="M6.6 10.8a15.2 15.2 0 0 0 6.6 6.6l2.2-2.2c.3-.3.7-.4 1-.2 1.1.4 2.3.6 3.6.6.6 0 1 .4 1 1V20c0 .6-.4 1-1 1A17 17 0 0 1 3 4c0-.6.4-1 1-1h3.5c.6 0 1 .4 1 1 0 1.3.2 2.5.6 3.6.1.3 0 .7-.2 1z"/></svg>
      682-555-0148
    </li>
    <li>
      <svg viewBox="0 0 24 24" fill="none" stroke="#e3222b" stroke-width="2"><circle cx="12" cy="12" r="10" fill="#e3222b"/><path d="M2 12h20M12 2c3 3 3 17 0 20M12 2c-3 3-3 17 0 20" stroke="#1a1a1b" stroke-width="1.4"/></svg>
      www.copperleafroofing.co
    </li>
    <li>
      <svg viewBox="0 0 24 24" fill="#e3222b"><path d="M2 9l10 6 10-6v12H2z"/><path d="M2 8l10-6 10 6-10 6z" opacity=".7"/></svg>
      dean@copperleafroofing.co
    </li>
  </ul>
</section>

</body>
</html>
```